Visitenkarten-Design für Steuerberater und Wirtschaftsprüfer
Thank you so much! Great communication, very fast and nice contact!
Zielgruppe
Steuerberater, Wirtschaftsprüfer in München
Aufgabenstellung
Wir haben ein Logo das uns gefällt, jetzt allerdings steht die Umfirmierung vor der Tür und aus der Kanzlei Zelliger (so unser Name) wird Zelliger und Partner mbB (die Jugend kommt mit als Partner in die Kanzlei) , Steuerberater, Wirtschaftsprüfer
Analog unseres alten Briefpapiers und der alten Visitenkarten soll eigentlich nur der Zusatz 'und Partner mbB' oder '& Partner mbB' gestaltet werden.
Das Dateiformat bei Visitenkarten bitte so übergeben, dass wir Namen selbst austauschen mit gängigen Officeprogrammen austauschen können. Bei den Visitenkarten ist das große 'Zelliger' geprägt.
Ich stelle das Logo, das aktuelle Briefpapier und aktuelle Visitenkarten ein. Unsere Farbe ist grau.
Das Logo bitte in .pdf, .png, .psd und .eps (sagt mi alles nichts, haben wir aber alles schon mal irgendwo gebraucht) , Visiten karten auch in .pddf und .ai
Bei Fragen kontaktiert mich gern jederzeit.

```html
<!DOCTYPE html>
<html lang="de">
<head>
<meta charset="utf-8">
<title>Zelliger &amp; Partner mbB – Visitenkarten</title>
<link rel="stylesheet" href="https://fonts.googleapis.com/css2?family=Questrial&family=Fira+Sans+Condensed:wght@600&display=swap">
<style>
  :root {
    --stage: #1e1e1e;
    --card: #5a5b5d;
    --ink-bright: #f2f2f2;
    --ink-soft: #d6d6d6;
    --ink-muted: #bcbcbc;
    --emboss: #a2a2a2;
  }
  * { margin: 0; padding: 0; box-sizing: border-box; }
  html, body {
    width: 1101px; height: 1200px; overflow: hidden;
    background: var(--stage);
    font-family: "Questrial", "Century Gothic", sans-serif;
  }
  .card {
    position: absolute; left: 194px; width: 711px; height: 473px;
    background: var(--card);
  }
  .card--front { top: 84px; }
  .card--back { top: 634px; }

  .brand { position: absolute; left: 0; right: 0; text-align: center; }
  .brand__name {
    display: inline-block; line-height: 1; letter-spacing: 2px;
    font-family: "Questrial", sans-serif; font-weight: 400;
    transform-origin: center;
  }
  .brand__line { display: block; white-space: nowrap; }
  .brand__legal {
    font-family: "Fira Sans Condensed", "Arial Narrow", sans-serif;
    font-weight: 600;
  }
  .brand__services { letter-spacing: 0.2px; }

  .card--front .brand { top: 43px; color: var(--ink-bright); }
  .card--front .brand__name { font-size: 124px; transform: scaleX(0.78); }
  .card--front .brand__line { margin-top: -12px; font-size: 15px; padding-left: 10px; }
  .card--front .brand__legal { font-size: 23px; }

  .card--back .brand { top: 61px; color: var(--emboss); }
  .card--back .brand__name { font-size: 136px; transform: scaleX(0.8); }
  .card--back .brand__line { margin-top: -18px; font-size: 16.5px; }
  .card--back .brand__legal { font-size: 27px; }

  .person {
    position: absolute; left: 0; right: 0; top: 272px; text-align: center;
    color: var(--ink-bright);
  }
  .person__degree { font-size: 15px; color: var(--ink-soft); }
  .person__name { font-size: 32px; }
  .person__role { display: block; font-size: 16px; color: var(--ink-soft); margin-top: 2px; }

  .divider {
    position: absolute; left: 158px; width: 418px; top: 375px;
    border-top: 1px solid var(--ink-soft);
  }
  .contact {
    position: absolute; left: 0; right: 0; top: 392px; text-align: center;
    font-size: 20px; line-height: 26px; color: var(--ink-bright); font-style: normal;
  }

  .web {
    position: absolute; top: 420px; left: 0; right: 0;
    font-size: 18px; color: var(--ink-muted);
  }
  .web span { position: absolute; white-space: nowrap; }
  .web__site { left: 76px; }
  .web__sep { left: 330px; }
  .web__mail { left: 378px; }
</style>
</head>
<body>
  <section class="card card--front">
    <div class="brand">
      <span class="brand__name">ZELLIGER</span>
      <span class="brand__line"><span class="brand__legal">&amp; PARTNER mbB</span> <span class="brand__services">| STEUERBERATER | WIRTSCHAFTSPRÜFER</span></span>
    </div>
    <div class="person">
      <span class="person__degree">Dipl.-Kfm</span> <span class="person__name">Lukas M. Zelliger</span>
      <span class="person__role">Steuerberater/Wirtschaftsprüfer</span>
    </div>
    <div class="divider"></div>
    <address class="contact">
      Lindenhain-Straße 22&nbsp; I 80337 München<br>
      T&nbsp; 089 - 47 21 3300 I F 089 - 47 21 3310
    </address>
  </section>

  <section class="card card--back">
    <div class="brand">
      <span class="brand__name">ZELLIGER</span>
      <span class="brand__line"><span class="brand__legal">&amp; PARTNER mbB</span> <span class="brand__services">| STEUERBERATER | WIRTSCHAFTSPRÜFER</span></span>
    </div>
    <div class="web">
      <span class="web__site">www.kanzlei-zelliger.com</span>
      <span class="web__sep">I</span>
      <span class="web__mail">email: info@kanzlei-zelliger.com</span>
    </div>
  </section>
</body>
</html>
```